TA BRAMLEY BUSINESS CARD DESIGN PROJECT

We need to utilize our logo that was expertly created on PixelHarbor and now need to match this with a business card design.

```html
<!DOCTYPE html>
<html lang="en">
<head>
<meta charset="utf-8">
<title>TA BRAMLEY Business Card</title>
<link href="https://fonts.googleapis.com/css2?family=Open+Sans:wght@400;700&display=swap" rel="stylesheet">
<style>
  :root {
    --page-bg: #e4e4e2;
    --card-white: #ffffff;
    --brand-blue: #1c5bb5;
    --brand-blue-dark: #15479a;
    --brand-blue-light: #3d7fd0;
    --divider: #9fb7d9;
    --text-grey: #6b6b6b;
  }
  * { box-sizing: border-box; margin: 0; padding: 0; }
  html, body { width: 1200px; height: 801px; overflow: hidden; }
  body {
    background: var(--page-bg);
    font-family: "Open Sans", sans-serif;
    position: relative;
  }
  .card {
    position: absolute;
    top: 252px;
    width: 520px;
    height: 297px;
    box-shadow: 0 6px 18px rgba(0,0,0,0.15);
  }
  .card-front {
    left: 50px;
    background: var(--card-white);
    border-bottom: 3px solid var(--brand-blue);
  }
  .card-back {
    left: 630px;
    background: var(--brand-blue);
    overflow: hidden;
  }
  .front-wordmark {
    position: absolute;
    left: 48px;
    top: 62px;
    color: var(--brand-blue);
    font-weight: 700;
    font-size: 34px;
    letter-spacing: 6px;
    line-height: 1.05;
  }
  .front-wordmark span { display: block; }
  .holder {
    position: absolute;
    left: 48px;
    bottom: 46px;
  }
  .holder-name {
    color: var(--brand-blue);
    font-weight: 700;
    font-size: 17px;
    letter-spacing: 0.5px;
  }
  .holder-title {
    color: var(--text-grey);
    font-size: 13px;
    margin-top: 2px;
  }
  .divider {
    position: absolute;
    left: 292px;
    top: 96px;
    width: 1px;
    height: 104px;
    background: var(--divider);
  }
  .contact-list {
    position: absolute;
    left: 316px;
    top: 106px;
    list-style: none;
  }
  .contact-item {
    display: flex;
    align-items: center;
    gap: 8px;
    color: var(--text-grey);
    font-size: 13px;
    line-height: 28px;
  }
  .contact-icon { width: 12px; height: 12px; fill: var(--brand-blue); }
  .back-pattern {
    position: absolute;
    inset: 0;
    background: linear-gradient(100deg, var(--brand-blue-dark) 0%, var(--brand-blue) 50%, var(--brand-blue-light) 100%);
  }
  .back-wordmark {
    position: absolute;
    right: 64px;
    bottom: 70px;
    color: var(--card-white);
    font-weight: 700;
    font-size: 20px;
    letter-spacing: 2px;
  }
</style>
</head>
<body>
  <section class="card card-front">
    <div class="front-wordmark"><span>TA</span><span>BRAMLEY</span></div>
    <div class="holder">
      <p class="holder-name">DANA WHITFORD</p>
      <p class="holder-title">President</p>
    </div>
    <div class="divider"></div>
    <ul class="contact-list">
      <li class="contact-item">
        <svg class="contact-icon" viewBox="0 0 12 12"><circle cx="6" cy="6" r="6"/><path d="M3.6 3.2l1.2-.2.6 1.4-.7.6c.4.9 1 1.5 1.9 1.9l.6-.7 1.4.6-.2 1.2c-3 .2-5-1.8-4.8-4.8z" fill="#fff"/></svg>
        555-014-2289
      </li>
      <li class="contact-item">
        <svg class="contact-icon" viewBox="0 0 12 12"><rect x="0" y="2" width="12" height="8" rx="1"/><path d="M0.5 2.5L6 7l5.5-4.5" stroke="#fff" fill="none"/></svg>
        d.whitford@tabramley.com
      </li>
      <li class="contact-item">
        <svg class="contact-icon" viewBox="0 0 12 12"><circle cx="6" cy="6" r="6"/><path d="M1 6h10M6 1c-2.5 3-2.5 7 0 10M6 1c2.5 3 2.5 7 0 10" stroke="#fff" stroke-width="0.8" fill="none"/></svg>
        www.tabramley.com
      </li>
    </ul>
  </section>

  <section class="card card-back">
    <div class="back-pattern" role="img" aria-label="Repeating brand mark pattern in tonal blues"></div>
    <p class="back-wordmark">TA BRAMLEY</p>
  </section>
</body>
</html>
```